Calverbrook.com.au - Pelvane Australia - Uncoded PSD only

We need a web design for a virtual assistant company based in Sydney Australia called "Calverbrook". We provide virtual assistance and unlimited admin tasks to small business owners for a monthly fee. We would like to see designs that are not too different to www.pelvane.com. Words to describe the design and feel of this website are sleek and professional. We want to use bright inviting colours for the call to action buttons and a professional business focused background.

Target Market(s)

business executives, business owners, small business owners, those professionals who lack time.

Industry/Entity Type

Business Consultant

Number of Pages Required

3 page

Font styles to use
Sans Serif

Colors
5e5e5e
1b1b1b
3176b5
33b8a4

Requirements
Must have
• Call to action buttons, sleek business feel think snorbix.io and pelvane.com
Nice to have
• Bold back ground colours, bright call to action buttons
Should not have
• too much white

```html
<!DOCTYPE html>
<html lang="en">
<head>
<meta charset="utf-8">
<title>Calverbrook – Virtual Assistant Company</title>
<link rel="stylesheet" href="https://fonts.googleapis.com/css2?family=Open+Sans:wght@300;400;600;700&display=swap">
<style>
:root{
  --blue:#3176b5;
  --teal:#33b8a4;
  --ink:#1b1b1b;
  --text:#5e5e5e;
  --light:#f1f2f4;
  --grey:#e4e5e7;
  --navy:#1d3d63;
  --navy-deep:#152e4c;
  --white:#ffffff;
}
*{margin:0;padding:0;box-sizing:border-box}
html,body{width:1200px;height:3836px;overflow:hidden}
body{font-family:"Open Sans",Arial,sans-serif;color:var(--text);background:var(--white);position:relative}
section,header,footer{position:absolute;left:0;width:1200px;overflow:hidden}
.btn{display:inline-block;background:var(--teal);color:var(--white);font-size:15px;font-weight:600;letter-spacing:1px;text-transform:uppercase;padding:16px 34px;border-radius:3px;white-space:nowrap}
.section-title{font-size:30px;font-weight:700;color:var(--blue);letter-spacing:.5px;text-transform:uppercase}
.body-copy{font-size:15px;line-height:26px;color:var(--text)}
.photo{position:absolute}

/* hero */
.hero{top:0;height:660px}
.hero .photo{inset:0;background:linear-gradient(180deg,#5b6f86 0%,#3f566f 40%,#2c3f53 70%,#39506a 100%)}
.hero .shade{position:absolute;inset:0;background:rgba(20,30,45,.35)}
.nav{position:absolute;top:44px;left:100px;right:100px;display:flex;justify-content:space-between;align-items:center}
.brand{font-size:34px;font-weight:400;color:var(--white);letter-spacing:.5px}
.menu{display:flex;gap:52px;list-style:none}
.menu li{font-size:14px;font-weight:600;color:var(--white);letter-spacing:.5px}
.hero-copy{position:absolute;top:180px;left:0;width:1200px;text-align:center;color:var(--white)}
.hero-copy h1{font-size:46px;font-weight:700;letter-spacing:2px;line-height:54px}
.hero-copy h2{font-size:46px;font-weight:300;letter-spacing:2px;line-height:56px}
.hero-copy p{width:660px;margin:14px auto 0;font-size:19px;line-height:28px}
.play{position:absolute;top:384px;left:568px}
.hero .btn{position:absolute;top:480px;left:468px;width:264px;text-align:center;padding:17px 0}

/* welcome */
.welcome{top:660px;height:580px;background:var(--white)}
.welcome .section-title{position:absolute;top:130px;left:100px}
.welcome .body-copy{position:absolute;top:186px;left:100px;width:440px}
.welcome .btn{position:absolute;top:390px;left:100px}
.welcome .photo{left:480px;top:28px;width:720px;height:520px;background:radial-gradient(ellipse at 60% 45%,#dfe6ee 0%,#c9d4e0 40%,#f4f6f8 75%,#ffffff 100%)}

/* what we do */
.services{top:1240px;height:460px;background:var(--blue);color:var(--white)}
.services .section-title{color:var(--white);text-align:center;width:100%;position:absolute;top:58px}
.services .intro{position:absolute;top:112px;left:140px;width:920px;text-align:center;font-size:14px;line-height:24px}
.service-list{position:absolute;top:224px;left:100px;width:1000px;display:flex;justify-content:space-between}
.service{width:290px}
.service h3{display:flex;align-items:center;gap:14px;font-size:14px;font-weight:700;letter-spacing:.5px}
.service p{margin-top:14px;font-size:13px;line-height:22px}
.pager{position:absolute;top:398px;left:0;width:100%;display:flex;justify-content:center;gap:10px}
.pager span{width:9px;height:9px;border-radius:50%;background:rgba(255,255,255,.45)}
.pager span.on{background:var(--white)}

/* benefits */
.benefits{top:1700px;height:492px;background:var(--light)}
.benefits .photo{left:100px;top:100px;width:520px;height:300px;background:linear-gradient(135deg,#7d6a55 0%,#4a4038 50%,#2c2a28 100%);border-radius:4px}
.benefits .section-title{position:absolute;top:94px;left:680px}
.benefit-list{position:absolute;top:150px;left:680px;width:420px;list-style:none}
.benefit-list li{display:flex;gap:14px;font-size:13px;line-height:21px;margin-bottom:16px}
.benefit-list svg{flex:none;margin-top:4px}

/* vision */
.vision{top:2192px;height:400px}
.vision .photo{inset:0;background:linear-gradient(90deg,#3a3f47 0%,#565b62 35%,#4a4e55 65%,#2e3238 100%)}
.vision .shade{position:absolute;inset:0;background:rgba(15,18,24,.5)}
.vision .section-title{position:absolute;top:96px;width:100%;text-align:center;color:var(--white)}
.vision p{position:absolute;top:146px;left:190px;width:820px;text-align:center;font-size:14px;line-height:24px;color:var(--white)}
.vision .btn{position:absolute;top:246px;left:508px}

/* about */
.about{top:2592px;height:408px;background:var(--white)}
.about .section-title{position:absolute;top:118px;left:100px}
.about .body-copy{position:absolute;top:168px;left:100px;width:370px;font-size:14px;line-height:24px}
.about .btn{position:absolute;top:326px;left:100px}
.about .photo{left:480px;top:0;width:720px;height:408px;background:linear-gradient(160deg,#ffffff 0%,#eceff2 35%,#c7ccd2 70%,#e9ebee 100%)}

/* testimonials */
.testimonials{top:3000px;height:420px;background:var(--grey)}
.testimonials .section-title{position:absolute;top:110px;width:100%;text-align:center}
.testimonials .intro{position:absolute;top:160px;width:100%;text-align:center;font-size:14px}
.quotes{position:absolute;top:246px;left:100px;width:1000px;display:flex;justify-content:space-between}
.quote{width:300px;display:flex;gap:22px}
.avatar{flex:none;width:78px;height:78px;border-radius:50%;background:linear-gradient(160deg,#c9a88c,#7a5e48)}
.quote h4{font-size:12px;font-weight:700;color:var(--teal);letter-spacing:.5px}
.quote .role{font-size:11px;color:var(--blue);margin-top:2px}
.quote p{font-size:12px;line-height:20px;margin-top:8px}

/* partners */
.partners{top:3420px;height:100px;background:var(--white);display:flex;align-items:center;justify-content:space-between;padding:0 60px}
.partner{height:30px;border-radius:4px;background:#c3cad3}

/* footer */
.site-footer{top:3520px;height:316px;background:var(--navy);color:#d4dde8}
.footer-cols{position:absolute;top:48px;left:100px;width:1000px;display:flex;justify-content:space-between}
.footer-col h5{font-size:14px;font-weight:700;color:var(--white);letter-spacing:.5px;margin-bottom:18px}
.footer-col p,.footer-col li{font-size:12px;line-height:22px;list-style:none}
.col-about{width:250px}.col-links{width:150px}.col-contact{width:230px}.col-follow{width:190px}
.contact-line{display:flex;gap:10px;align-items:center;margin-bottom:6px}
.socials{display:flex;gap:10px;margin-top:14px}
.socials span{width:30px;height:30px;border-radius:50%;background:#8ea3bb}
.footer-bar{position:absolute;bottom:0;left:0;width:100%;height:36px;background:var(--navy-deep);font-size:11px;text-align:center;line-height:36px;color:#b8c5d4}
</style>
</head>
<body>

<header class="hero">
  <div class="photo" role="img" aria-label="Sydney harbour skyline at dusk with the opera house"></div>
  <div class="shade"></div>
  <nav class="nav">
    <div class="brand">calverbrook</div>
    <ul class="menu"><li>HOME</li><li>ABOUT US</li><li>WHAT WE DO?</li><li>TESTIMONIALS</li><li>BLOG</li><li>CONTACT US</li></ul>
  </nav>
  <div class="hero-copy">
    <h1>WE ARE A</h1>
    <h2>VIRTUAL ASSISTANT COMPANY</h2>
    <p>Based in Sydney Australia, We provide virtual assistance and unlimited admin tasks to small business owners for a monthly fee.</p>
  </div>
  <svg class="play" width="64" height="64" viewBox="0 0 64 64"><circle cx="32" cy="32" r="29" fill="none" stroke="#fff" stroke-width="3" opacity=".85"/><path d="M26 20 L45 32 L26 44 Z" fill="#fff" opacity=".85"/></svg>
  <span class="btn">Request a consultation</span>
</header>

<section class="welcome">
  <div class="photo" role="img" aria-label="Smiling businessman in glasses working at a laptop"></div>
  <h2 class="section-title">Welcome to Calverbrook</h2>
  <p class="body-copy">Our team of skilled assistants takes the daily admin off your desk so you can focus on growing your business. From inbox and calendar management to bookings, data entry and research, we handle the tasks that slow you down, quickly and reliably, every single day.</p>
  <span class="btn">View our history</span>
</section>

<section class="services">
  <h2 class="section-title">What we do ?</h2>
  <p class="intro">We give busy owners a dedicated assistant for a flat monthly fee. Hand over as many admin tasks as you need, with no contracts, no hiring costs and no training time. Simple support that scales as your business grows.</p>
  <div class="service-list">
    <div class="service">
      <h3><svg width="26" height="26" viewBox="0 0 26 26" fill="none" stroke="#fff" stroke-width="2"><path d="M13 3 L23 8 L13 13 L3 8 Z"/><path d="M3 13 L13 18 L23 13"/><path d="M3 18 L13 23 L23 18"/></svg>LOREM IPSUM IS SIMPLE</h3>
      <p>Email, diary and inbox care handled daily by your assistant, so nothing is missed.</p>
    </div>
    <div class="service">
      <h3><svg width="26" height="26" viewBox="0 0 26 26" fill="none" stroke="#fff" stroke-width="2"><circle cx="13" cy="13" r="4"/><path d="M13 2v4M13 20v4M2 13h4M20 13h4M5 5l3 3M18 18l3 3M5 21l3-3M18 8l3-3"/></svg>LOREM IPSUM IS SIMPLE</h3>
      <p>Bookings, invoices and data entry kept in order with clear weekly reporting.</p>
    </div>
    <div class="service">
      <h3><svg width="28" height="26" viewBox="0 0 28 26" fill="none" stroke="#fff" stroke-width="2"><rect x="5" y="5" width="18" height="12" rx="1"/><path d="M2 21h24"/></svg>LOREM IPSUM IS SIMPLE</h3>
      <p>Research, travel plans and customer follow ups done online by trusted staff.</p>
    </div>
  </div>
  <div class="pager"><span class="on"></span><span></span><span></span></div>
</section>

<section class="benefits">
  <div class="photo" role="img" aria-label="Laptop screen showing a businessman reading a document"></div>
  <h2 class="section-title">Benifits</h2>
  <ul class="benefit-list">
    <li><svg width="14" height="12" viewBox="0 0 14 12"><path d="M1 6 L5 10 L13 1" fill="none" stroke="#33b8a4" stroke-width="2.4"/></svg>Save hours every week by handing routine admin to a trained assistant.</li>
    <li><svg width="14" height="12" viewBox="0 0 14 12"><path d="M1 6 L5 10 L13 1" fill="none" stroke="#33b8a4" stroke-width="2.4"/></svg>One flat monthly fee with unlimited tasks and no hidden extras.</li>
    <li><svg width="14" height="12" viewBox="0 0 14 12"><path d="M1 6 L5 10 L13 1" fill="none" stroke="#33b8a4" stroke-width="2.4"/></svg>No hiring, payroll or office space needed to get support started.</li>
    <li><svg width="14" height="12" viewBox="0 0 14 12"><path d="M1 6 L5 10 L13 1" fill="none" stroke="#33b8a4" stroke-width="2.4"/></svg>Local Sydney team working in your time zone and business hours.</li>
    <li><svg width="14" height="12" viewBox="0 0 14 12"><path d="M1 6 L5 10 L13 1" fill="none" stroke="#33b8a4" stroke-width="2.4"/></svg>Secure handling of your accounts, files and client information.</li>
  </ul>
</section>

<section class="vision">
  <div class="photo" role="img" aria-label="Business team meeting around a table in an office"></div>
  <div class="shade"></div>
  <h2 class="section-title">Our Vision</h2>
  <p>We want every small business owner to have the support of a full office team without the cost. By taking care of the admin, we free leaders to spend their time on clients, growth and the work they love most.</p>
  <span class="btn">Read more info</span>
</section>

<section class="about">
  <div class="photo" role="img" aria-label="Hands typing on a laptop while holding a smartphone"></div>
  <h2 class="section-title">About Calverbrook</h2>
  <p class="body-copy">Calverbrook began in Sydney to help owners who were buried in paperwork. Today our assistants support businesses across Australia with friendly, dependable admin help. We learn how you work and treat your business as our own.</p>
  <span class="btn">View our info</span>
</section>

<section class="testimonials">
  <h2 class="section-title">Testimonials</h2>
  <p class="intro">Here is what a few of our clients have to say about working with our assistants every day.</p>
  <div class="quotes">
    <div class="quote"><div class="avatar" role="img" aria-label="Client portrait"></div><div><h4>DAMIEN HOLT</h4><div class="role">Business Owner</div><p>Our inbox and calendar are finally under control. I now get whole days back each week.</p></div></div>
    <div class="quote"><div class="avatar" role="img" aria-label="Client portrait"></div><div><h4>MARA QUINLEY</h4><div class="role">Practice Manager</div><p>Fast, friendly and accurate. Our assistant feels like part of the team already.</p></div></div>
    <div class="quote"><div class="avatar" role="img" aria-label="Client portrait"></div><div><h4>JASPER VALE</h4><div class="role">Company Director</div><p>The flat fee made the decision easy, and the service has been excellent.</p></div></div>
  </div>
</section>

<section class="partners">
  <div class="partner" style="width:90px"></div>
  <div class="partner" style="width:80px"></div>
  <div class="partner" style="width:96px"></div>
  <div class="partner" style="width:84px"></div>
  <div class="partner" style="width:100px"></div>
  <div class="partner" style="width:86px"></div>
  <div class="partner" style="width:92px"></div>
</section>

<footer class="site-footer">
  <div class="footer-cols">
    <div class="footer-col col-about"><h5>WHO WE ARE ?</h5><p>A Sydney based virtual assistant company giving small business owners unlimited admin help for one monthly fee. Friendly, local and trusted support.</p></div>
    <div class="footer-col col-links"><h5>WELCOME</h5><ul><li>Home</li><li>About Us</li><li>What we do</li><li>Testimonials</li><li>Blog</li><li>Contact Us</li></ul></div>
    <div class="footer-col col-contact"><h5>GET IN TOUCH</h5>
      <p class="contact-line"><svg width="12" height="14" viewBox="0 0 12 14"><path d="M6 1a4.5 4.5 0 0 1 4.5 4.5C10.5 9 6 13 6 13S1.5 9 1.5 5.5A4.5 4.5 0 0 1 6 1z" fill="#d4dde8"/></svg>120 Harbour Lane, Sydney NSW 2000</p>
      <p class="contact-line"><svg width="12" height="12" viewBox="0 0 12 12"><path d="M2 1h3l1 3-2 1a7 7 0 0 0 3 3l1-2 3 1v3a1 1 0 0 1-1 1A10 10 0 0 1 1 2a1 1 0 0 1 1-1z" fill="#d4dde8"/></svg>1300 555 014</p>
      <p class="contact-line"><svg width="13" height="10" viewBox="0 0 13 10"><rect x=".5" y=".5" width="12" height="9" fill="none" stroke="#d4dde8"/><path d="M.5 .5 L6.5 5.5 L12.5 .5" fill="none" stroke="#d4dde8"/></svg>hello@calverbrook.com.au</p>
    </div>
    <div class="footer-col col-follow"><h5>FOLLOW US</h5><p>Connect with our team online</p><div class="socials"><span></span><span></span><span></span><span></span><span></span></div></div>
  </div>
  <div class="footer-bar">© 2015 Calverbrook.com.au · All rights reserved · Terms &amp; Conditions · Privacy Policy</div>
</footer>

</body>
</html>
```